Website for Dental Office - The Bright Arch Clinic

The bright arch clinic is a dental office offering cosmetic dentistry, general dentistry, and multi-specialty dental care all under one roof in our state-of-the-art cosmetic dental center. We are particularly striving to provide services that fit the need of the young generation. Thus, we hope to have a modern, professional concise website that represents our spirit.

*Should be able to switch from English to Chinese

6 sections besides homepage:
Home, Meet us, Services,
Patient Info, Cases&Reviews, Blog, Contact

The Services sections should contain multiple subsections such as cleaning and prevention, cosmetic dentistry, implant dentistry, removable dentures, etc...
The Patient Info section is also intended to contain several subsections such as
New Patient offer, accepted Insurance, patient portal, helpful tips, etc...

Target Market(s)

young generation

Coding

Coded - Design and coding required

Number of Pages Required

5+ page

Font styles to use
Sans Serif

Colors
0592cd
33a6d7
85cae6
00a990
33b8a4
86cfc6
cee9f5
cfeae6
3277b5

Requirements
Must have
• *Should be able to switch from English to Chinese
Nice to have
• http://www.thebrightarchclinic.com/
• As a reference, the above link is the current website, but we would like to change the appearance and the content (our new logo's picture is attached)

```html
<!DOCTYPE html>
<html lang="en">
<head>
<meta charset="utf-8">
<title>The Bright Arch Clinic</title>
<link href="https://fonts.googleapis.com/css2?family=Catamaran:wght@500;600;700;800&family=Lato:wght@400;700;900&display=swap" rel="stylesheet">
<style>
:root{
  --blue:#0592cd;
  --blue-mid:#33a6d7;
  --blue-deep:#3277b5;
  --green:#00a990;
  --green-mid:#33b8a4;
  --ink:#1d1d1d;
  --muted:#6b6b6b;
  --light:#efefef;
  --dark:#2b2d31;
  --white:#fff;
}
*{margin:0;padding:0;box-sizing:border-box}
html,body{width:1200px;height:3169px;overflow:hidden}
body{position:relative;font-family:'Lato',sans-serif;color:var(--ink);background:var(--white)}
.abs{position:absolute}
.head{font-family:'Catamaran',sans-serif}

/* hero */
.hero-photo{left:0;top:0;width:1200px;height:599px;background:linear-gradient(135deg,#6f7a86 0%,#9aa3ab 40%,#5d6a78 75%,#3d4856 100%)}
.hero-shape{left:0;top:0}
.logo{display:flex;align-items:center;gap:10px;color:var(--white);font-family:'Lato',sans-serif;font-weight:900;font-size:15px;letter-spacing:.2px}
.logo .mark{width:26px;height:26px;background:var(--white)}
.site-logo{left:161px;top:40px}
.nav{top:37px;left:419px;display:flex;gap:23px;font-size:12px;color:var(--white)}
.lang{left:979px;top:33px;width:60px;height:26px;background:var(--white);color:var(--blue);font-size:12px;font-weight:700;padding:5px 9px;display:flex;justify-content:space-between;align-items:center}
.lang::after{content:"";border:5px solid transparent;border-top:7px solid var(--blue);margin-top:6px}
.eyebrow{left:163px;top:226px;font-size:19px;font-weight:700;color:var(--white)}
.hero-title{left:161px;top:258px;font-size:54px;font-weight:700;color:var(--white);letter-spacing:.3px}
.hero-text{left:163px;top:330px;width:560px;font-size:11.5px;line-height:19px;color:var(--white)}
.btn-white{background:var(--white);color:var(--blue);font-family:'Catamaran',sans-serif;font-weight:700;display:flex;align-items:center;justify-content:center}
.hero-btn{left:161px;top:393px;width:135px;height:50px;font-size:19px}

/* services */
.card{top:670px;width:203px;height:240px;border:1px solid #d8d8d8;background:var(--white)}
.card .pic{height:112px}
.card h3{font-family:'Catamaran',sans-serif;font-weight:700;font-size:15px;padding:10px 12px 4px;letter-spacing:.3px}
.card p{font-size:11.5px;line-height:19px;color:var(--muted);padding:0 12px}
.card .more{font-size:11px;font-weight:700;color:var(--blue);padding:6px 12px;display:flex;align-items:center;gap:4px}
.card.active{background:var(--blue);border-color:var(--blue)}
.card.active h3,.card.active p,.card.active .more{color:var(--white)}
.btn-blue{background:var(--blue);color:var(--white);font-family:'Catamaran',sans-serif;font-weight:700;display:flex;align-items:center;justify-content:center}
.explore{left:543px;top:948px;width:114px;height:37px;font-size:15px}

/* about */
.about-bg{left:0;top:1049px;width:1200px;height:397px;background:var(--light)}
.about-title{left:162px;top:1100px;font-size:38px;font-weight:700}
.about-text{left:162px;top:1162px;width:430px;font-size:11.5px;line-height:19.6px;color:var(--muted)}
.about-text p+p{margin-top:19.6px}
.about-btn{left:161px;top:1352px;width:105px;height:37px;font-size:15px}
.about-photo{left:611px;top:1033px;width:434px;height:413px;background:radial-gradient(ellipse at 55% 45%,#f3e9df 0%,#dcdcdc 55%,#efefef 100%)}

/* patient info */
.pi-bg{left:0;top:1446px;width:1200px;height:509px;background:linear-gradient(120deg,#3d4550,#262b33 60%,#343b45)}
.section-title{width:1200px;left:0;text-align:center;font-family:'Catamaran',sans-serif;font-weight:700}
.pi-title{top:1494px;font-size:42px;color:var(--white)}
.field{width:282px;height:44px;border:1px solid var(--white);border-radius:3px;color:var(--white);font-size:11.5px;padding:0 12px;display:flex;align-items:center;justify-content:space-between}
.field .caret{border:5px solid transparent;border-top:8px solid var(--white);margin-top:6px}
.book{left:532px;top:1742px;width:174px;height:36px;font-size:15px}
.tile{top:1828px;width:203px;height:67px;color:var(--white);font-family:'Catamaran',sans-serif;font-weight:700;font-size:16px;letter-spacing:.3px;display:flex;align-items:center;justify-content:center}

/* testimonials */
.testi-title{top:1990px;font-size:40px}
.dot{left:160px;width:12px;height:12px;border:1.5px solid var(--blue);border-radius:50%}
.dot.on::after{content:"";position:absolute;left:2px;top:2px;width:5px;height:5px;background:var(--blue);border-radius:50%}
.avatar{left:562px;top:2064px;width:76px;height:76px;border-radius:50%;border:3px solid var(--blue);background:linear-gradient(#c9d3dc,#8f9ba6)}
.client{left:0;width:1200px;top:2151px;text-align:center;font-size:11.5px;font-weight:700;color:var(--blue)}
.quote-text{left:390px;top:2177px;width:420px;text-align:center;font-size:11.5px;line-height:19.6px;color:var(--muted)}
.qmark{font-family:'Catamaran',sans-serif;font-size:60px;font-weight:800;color:#c9c9c9;line-height:1}

/* team */
.team-bg{left:0;top:2311px;width:1200px;height:488px;background:linear-gradient(160deg,#5a5047,#2f2b28 55%,#403a35)}
.team-title{top:2362px;font-size:42px;color:var(--white)}
.member{top:2455px;width:278px;height:268px;background:var(--white)}
.member .pic{height:186px}
.member h4{font-family:'Lato',sans-serif;font-weight:700;font-size:14.5px;color:var(--blue);padding:20px 13px 4px}
.member p{font-size:11.5px;color:var(--muted);padding:0 13px}

/* footer */
.foot-bg{left:0;top:2799px;width:1200px;height:370px;background:var(--blue)}
.foot-logo{left:0;width:1200px;top:2866px;justify-content:center}
.foot-nav{top:2955px;left:0;width:1200px;display:flex;justify-content:center;gap:24px;font-size:12px;color:var(--white)}
.contact-now{left:462px;top:3016px;font-size:13px;font-weight:700;color:var(--white)}
.phone-ring{left:577px;top:3002px;width:46px;height:46px;border-radius:50%;background:var(--white);display:flex;align-items:center;justify-content:center}
.phone-num{left:648px;top:3012px;font-size:18px;font-weight:700;color:var(--white)}
.hours{left:0;width:1200px;top:3064px;text-align:center;font-size:11.5px;line-height:19px;font-weight:700;color:var(--white)}
.foot-rule{left:161px;top:3118px;width:878px;height:1px;background:rgba(255,255,255,.5)}
.copy{left:0;width:1200px;top:3136px;text-align:center;font-size:11.5px;font-weight:700;color:var(--white)}
</style>
</head>
<body>

<!-- Hero -->
<div class="abs hero-photo" role="img" aria-label="Photo of a dentist in a mask treating a smiling boy in a dental chair"></div>
<svg class="abs hero-shape" width="1200" height="811" viewBox="0 0 1200 811">
  <polygon points="0,0 707,0 0,811" fill="#3277b5"/>
</svg>
<div class="abs site-logo logo"><span class="mark"></span>THE BRIGHT ARCH CLINIC</div>
<nav class="abs nav"><span>Home</span><span>About Us</span><span>Services</span><span>Meet us</span><span>Patient Info</span><span>Cases&amp;Reviews</span><span>Blog</span><span>Contact</span></nav>
<div class="abs lang">Eng</div>
<div class="abs eyebrow head">THE BRIGHT ARCH CLINIC</div>
<h1 class="abs hero-title head">We Provide Perfect Smile</h1>
<p class="abs hero-text">Lorem Ipsum is simply dummy text of the printing and typesetting industry. Lorem Ipsum has been the industry's standard dummy text ever since the 1500s</p>
<div class="abs hero-btn btn-white">Contact Us</div>

<!-- Services -->
<div class="abs card" style="left:161px">
  <div class="pic" role="img" aria-label="Photo of a dentist treating a patient" style="background:linear-gradient(135deg,#3a4f6e,#6c89b0)"></div>
  <h3>Cleaning and Prevention</h3>
  <p>Lorem Ipsum is simply dummy text of the printing and typesetting industry.</p>
  <div class="more">Read More <svg width="16" height="10" viewBox="0 0 16 10"><path d="M0 5h14M10 1l4 4-4 4" stroke="currentColor" fill="none" stroke-width="1.3"/></svg></div>
</div>
<div class="abs card active" style="left:386px">
  <div class="pic" role="img" aria-label="Close-up photo of teeth with a dental mirror" style="background:linear-gradient(135deg,#f2a6a0,#e8e3dc 60%,#d98880)"></div>
  <h3>Cosmetic Dentistry</h3>
  <p>Lorem Ipsum is simply dummy text of the printing and typesetting industry.</p>
  <div class="more">Read More <svg width="16" height="10" viewBox="0 0 16 10"><path d="M0 5h14M10 1l4 4-4 4" stroke="currentColor" fill="none" stroke-width="1.3"/></svg></div>
</div>
<div class="abs card" style="left:611px">
  <div class="pic" role="img" aria-label="Illustration of a dental implant between teeth" style="background:linear-gradient(135deg,#c8474b,#ecdcd4 55%,#b83a3f)"></div>
  <h3>Implant Dentistry</h3>
  <p>Lorem Ipsum is simply dummy text of the printing and typesetting industry.</p>
  <div class="more">Read More <svg width="16" height="10" viewBox="0 0 16 10"><path d="M0 5h14M10 1l4 4-4 4" stroke="currentColor" fill="none" stroke-width="1.3"/></svg></div>
</div>
<div class="abs card" style="left:836px">
  <div class="pic" role="img" aria-label="Photo of a removable denture in a mouth" style="background:linear-gradient(135deg,#dcdcdc,#c99a90 60%,#9fbf3a)"></div>
  <h3>Removable Dentures</h3>
  <p>Lorem Ipsum is simply dummy text of the printing and typesetting industry.</p>
  <div class="more">Read More <svg width="16" height="10" viewBox="0 0 16 10"><path d="M0 5h14M10 1l4 4-4 4" stroke="currentColor" fill="none" stroke-width="1.3"/></svg></div>
</div>
<div class="abs explore btn-blue">Explore More</div>

<!-- About -->
<div class="abs about-bg"></div>
<div class="abs about-photo" role="img" aria-label="Photo of a dentist in safety glasses examining a patient"></div>
<h2 class="abs about-title head">About Us</h2>
<div class="abs about-text">
  <p>Welcome to The Bright Arch Clinic where we specialize in General and Cosmetic Dentistry, Dental Implants, Periodontics (Gum Surgery), Endodontics (Root Canal Treatment) and Reconstructive Dentistry for patients in Riverton, Ashford, Millbrook, Oakvale, Elmstead, Fairhaven, Westbury, Hollis and all other surrounding neighborhoods of Riverton, Eastmark.</p>
  <p>With Northgate and Linden credentials that inspire confidence, we offer cosmetic dentistry, general dentistry...</p>
</div>
<div class="abs about-btn btn-blue">Read More</div>

<!-- Patient Info -->
<div class="abs pi-bg" role="img" aria-label="Dimmed background photo of a dental treatment room"></div>
<h2 class="abs section-title pi-title">Patient Info</h2>
<div class="abs field" style="left:161px;top:1585px">Name:</div>
<div class="abs field" style="left:460px;top:1585px">Email</div>
<div class="abs field" style="left:759px;top:1585px;width:280px">Phone:</div>
<div class="abs field" style="left:161px;top:1645px">Time:</div>
<div class="abs field" style="left:460px;top:1645px">Service:<span class="caret"></span></div>
<div class="abs field" style="left:759px;top:1645px;width:280px">Date:</div>
<div class="abs book btn-white">Book An Appointment</div>
<div class="abs tile" style="left:161px;background:var(--blue)">NEWPATIENT OFFER</div>
<div class="abs tile" style="left:386px;background:var(--blue-deep)">ACCEPTED INSURANCE</div>
<div class="abs tile" style="left:611px;background:var(--green)">PATIENT PORTAL</div>
<div class="abs tile" style="left:836px;background:var(--green-mid)">HELPFUL TIPS</div>

<!-- Testimonials -->
<svg class="abs" style="left:0;top:1955px" width="1200" height="356" viewBox="0 1955 1200 356">
  <polygon points="172,1955 1200,1955 1027,2311 0,2311" fill="#efefef"/>
  <polygon points="98,1992 144,1992 98,2087" fill="#00a990"/>
  <polygon points="1123,2142 1123,2283 1055,2283" fill="#00a990"/>
</svg>
<h2 class="abs section-title testi-title">Testimonials</h2>
<div class="abs dot" style="top:2084px"></div>
<div class="abs dot" style="top:2114px"></div>
<div class="abs dot on" style="top:2144px"></div>
<div class="abs dot" style="top:2174px"></div>
<div class="abs avatar" role="img" aria-label="Client portrait photo"></div>
<div class="abs client">-Client Name</div>
<div class="abs qmark" style="left:338px;top:2130px">&ldquo;</div>
<p class="abs quote-text">Lorem Ipsum is simply dummy text of the printing and typesetting industry. Lorem Ipsum has been the industry's standard dummy text ever since the 1500s, when an unknown printer took a galley of type and scrambled it to make a type specimen book.</p>
<div class="abs qmark" style="left:832px;top:2236px">&rdquo;</div>

<!-- Team -->
<div class="abs team-bg" role="img" aria-label="Dimmed background photo of a dental clinic"></div>
<h2 class="abs section-title team-title">Our Team</h2>
<div class="abs member" style="left:161px">
  <div class="pic" role="img" aria-label="Portrait photo of the orthodontist" style="background:linear-gradient(135deg,#c9b8a2,#8a7565)"></div>
  <h4>NADIA VERHOEF, DMD, MS</h4><p>Board Certified Orthodontist</p>
</div>
<div class="abs member" style="left:461px">
  <div class="pic" role="img" aria-label="Portrait photo of the pediatric dentist" style="background:linear-gradient(135deg,#d9d9d9,#8c8c8c)"></div>
  <h4>THEO MARCHETTI, DMD</h4><p>Board Certified, Pediatric Dentist, Orthodontist</p>
</div>
<div class="abs member" style="left:761px">
  <div class="pic" role="img" aria-label="Portrait photo of the general dentist" style="background:linear-gradient(135deg,#e9e6e2,#a88d78)"></div>
  <h4>DR. LINA OKAFOR, DMD</h4><p>General Dentist</p>
</div>

<!-- Footer -->
<div class="abs foot-bg"></div>
<div class="abs foot-logo logo" style="display:flex"><span class="mark"></span>THE BRIGHT ARCH CLINIC</div>
<nav class="abs foot-nav"><span>Home</span><span>About Us</span><span>Services</span><span>Meet us</span><span>Patient Info</span><span>Cases&amp;Reviews</span><span>Blog</span><span>Contact</span></nav>
<div class="abs contact-now">Contact Us Now</div>
<div class="abs phone-ring">
  <svg width="22" height="22" viewBox="0 0 24 24"><path d="M6.6 10.8a15 15 0 0 0 6.6 6.6l2.2-2.2a1 1 0 0 1 1-.25 11.4 11.4 0 0 0 3.6.57 1 1 0 0 1 1 1V20a1 1 0 0 1-1 1A17 17 0 0 1 3 4a1 1 0 0 1 1-1h3.5a1 1 0 0 1 1 1c0 1.25.2 2.45.57 3.57a1 1 0 0 1-.25 1z" fill="#0592cd"/></svg>
</div>
<div class="abs phone-num">555.214.0187</div>
<div class="abs hours">Mon- Fri : 9.30 am to 7.00 pm<br>Sat, Sun : Closed</div>
<div class="abs foot-rule"></div>
<div class="abs copy">© 2019. The Bright Arch Clinic. All Rights Reserved, Privacy Policy.</div>

</body>
</html>
```